July 2022 Industrial Manufacturer Product Expo Mexico City

We manufacture large screws and fastners for large Mining equipment, Trains, large ships, airplanes, wind turbines, and so on. We also do custom work base on the customer needs. No matter the size we can make it.
We have a Expo coming up with companies all over the world. We have to stand out we are a family own business so our customer service will be above and beyond anyone can provide. We do not have a sales force to push our products and services we provide one on one service.
Plus@!! I'm looking for anything that you designers can come up with if it was your company to put on a business card, plus i want to do a 1 or 2 sided pamphlet, and then a website. We make Speciality Bolts for large mining equipment these bolts can be 3 to 4 foot long!!! Plus fasteners, Nuts, washers, any, size, strengths, special materials, we offer more of a ono on one customer service, We are a small company, family own, but can fulfill any type of orders. We can also provide special time lines for emergency orders. "We keep the machines running we here at KRV don't believe in down time" We want to hear any slogan based on our company to stand out.
Thanks i really appreciate all your work and options that we have to pick on. Plus just a thought we could possibly want to entertain a experience Marketing internet help maybe a employment possibility. Thanks

I need 2 cards one in Spanish and English Like the steel back ground maybe send me in some bright red and blue writing Same with the Black cards Please remove the word Military The logo KRV maybe integrate a picture of a Bolt 🔩 Thank you

Still looking for I need 2 cards one in Spanish and English Like the steel back ground maybe send me in some bright red and blue writing Same with the Black cards try bright writing Please remove the word Military The logo KRV maybe integrate a picture of a Bolt 🔩 Plus will need the company to make a brochure and website next Thank you

Target Market(s)

Large Mining, Ship, Train, Green Energy, VELM, and Government equipment. Throughout the World

Industry/Entity Type

We can Custom Manufacture any type of Fastners for Mining equipment, Trains, Ships, Green energy, Governments, or military projects. wind turbines,

Contact Information for Business Card

I attached the name and contact info that's on a card, plus the Company Logo. Would like industrial looking background with Bright Colors that will stand out!! If we can insert somewhere maybe on back that we "Custom Manufacture Any Size or Quantity Fastners for Large Mining Equipment, Trains, Ships, Green Energy Equipment or Government Projects

Font styles to use
Other font styles liked:
• You Pick, has to be bold, colorful standout, Professional looking Beable to read it.

Colors

Designer to choose colors to be used in the design.

Requirements
Must have
• Need in Spanish and English TO STANDOUT FROM THE REST OF THE EXPO!! See Business card details, Rounded corners
Nice to have
• Can i see some of the darker cards with Bright Red and Blue letters I like to see the different type of card material, heavy thickness, plastic, transparent, Metal types, Bright Colors, I saw like Raised letters like on the logo.

```html
<!DOCTYPE html>
<html lang="es">
<head>
<meta charset="utf-8">
<title>KRV Business Cards</title>
<link href="https://fonts.googleapis.com/css2?family=Exo+2:wght@300;400;500;600&display=swap" rel="stylesheet">
<style>
  :root {
    --stage: #2a2624;
    --card: #1c1c1e;
    --blue: #1a8fd8;
    --blue-deep: #0a3fb0;
    --blue-bright: #1596e6;
    --red-bright: #ff2a2a;
    --steel: #6e6f74;
    --text-light: #e6e6e8;
    --rule: #55565a;
  }
  * { margin: 0; padding: 0; box-sizing: border-box; }
  html, body {
    width: 1200px; height: 842px; overflow: hidden;
    background: var(--stage);
    font-family: "Exo 2", Arial, sans-serif;
  }
  .canvas {
    position: relative; width: 1200px; height: 842px;
    display: flex; align-items: center; justify-content: center; gap: 56px;
  }
  .card {
    position: relative; width: 520px; height: 297px;
    background: var(--card); border-radius: 10px; overflow: hidden;
    box-shadow: 0 10px 30px rgba(0,0,0,.45);
  }

  /* Contact side */
  .band {
    position: absolute; left: 0; right: 0; height: 11px;
    background: linear-gradient(to bottom, var(--blue-deep), var(--blue-bright));
  }
  .band--top { top: 0; }
  .band--bottom { bottom: 0; background: linear-gradient(to top, var(--blue-deep), var(--blue-bright)); }
  .contact {
    position: absolute; inset: 0;
    display: flex; flex-direction: column; align-items: center; justify-content: center;
    text-align: center; padding: 0 30px;
  }
  .contact__name { color: var(--blue); font-size: 26px; font-weight: 400; letter-spacing: .5px; line-height: 1.2; }
  .contact__role { color: var(--text-light); font-size: 15px; font-weight: 300; margin-top: 4px; line-height: 1.3; }
  .contact__email { color: var(--text-light); font-size: 15px; font-weight: 300; line-height: 1.3; }
  .contact__rule { width: 150px; height: 1px; background: var(--rule); margin: 12px 0 10px; }
  .contact__phones { display: grid; grid-template-columns: auto auto; column-gap: 8px; text-align: left; line-height: 1.2; }
  .phone__label { color: var(--red-bright); font-size: 19px; font-weight: 600; }
  .phone__number { color: var(--text-light); font-size: 20px; font-weight: 300; letter-spacing: 1px; }

  /* Brand side */
  .accent {
    position: absolute; width: 14px; height: 48px;
    background: linear-gradient(to bottom, var(--blue-deep), var(--blue-bright));
  }
  .accent::after {
    content: ""; position: absolute; top: 0; width: 3px; height: 100%; background: var(--steel);
  }
  .accent--left { left: 0; top: 150px; }
  .accent--left::after { right: -6px; }
  .accent--right { right: 0; top: 60px; }
  .accent--right::after { left: -6px; }
  .brand {
    position: absolute; inset: 0;
    display: flex; flex-direction: column; align-items: center; justify-content: center;
    padding: 0 40px;
  }
  .brand__name {
    display: flex; align-items: center; gap: 14px;
    color: var(--steel); font-size: 64px; font-weight: 600; letter-spacing: 8px; line-height: 1;
  }
  .brand__mark { width: 14px; height: 14px; background: var(--red-bright); }
  .brand__tagline {
    margin-top: 26px; color: var(--text-light); font-size: 13px; font-weight: 400;
    text-align: center; line-height: 1.4; max-width: 440px;
  }
</style>
</head>
<body>
<main class="canvas">
  <section class="card card--contact">
    <div class="band band--top"></div>
    <div class="contact">
      <p class="contact__name">Lic.Daniela Ortega Ruiz</p>
      <p class="contact__role">Cotizaciones en / Quotes at</p>
      <p class="contact__email">krvtornilleria.ventas@mail.com</p>
      <div class="contact__rule"></div>
      <div class="contact__phones">
        <span class="phone__label">P:</span><span class="phone__number">5550193601</span>
        <span class="phone__label">M:</span><span class="phone__number">5550827600</span>
      </div>
    </div>
    <div class="band band--bottom"></div>
  </section>

  <section class="card card--brand">
    <div class="accent accent--left"></div>
    <div class="accent accent--right"></div>
    <div class="brand">
      <p class="brand__name"><span class="brand__mark"></span>KRV</p>
      <p class="brand__tagline">Custom Manufacture Any Size or Quantity Fastners for Large<br>Mining Equipment, Trains, Ships, Green Energy Equipment<br>or Government Projects</p>
    </div>
  </section>
</main>
</body>
</html>
```